A new presentation to our clients

we are a Real Estate agency, our website is www.lumibrasa.com and it’s time to have a new, fashion and remarcable Business Card. we want to differentiate ourselves from other companies so we want a business card that differentiates us. we want the business card to impact our customers. in the competitive market that we have today, we have to be different and it is this difference that we seek

Target Market(s)

Real Estate Clients

Contact Information for Business Card

We search a totaly diferent card from the usual

Font styles to use
Sans Serif

Colors
e34197

Requirements
Must have
• Logo, adress, phone contact, e-mail, photo, and our website
Nice to have
• We would like to see a modern business card
Should not have
• Houses or building draws

```html
<!DOCTYPE html>
<html lang="en">
<head>
<meta charset="utf-8">
<title>Lumi Brasa – Business Card</title>
<link href="https://fonts.googleapis.com/css2?family=Jost:wght@300;400;500&display=swap" rel="stylesheet">
<style>
  :root {
    --backdrop: #3a3a3a;
    --card: #ffffff;
    --pink: #e3237f;
    --pink-light: #ef5aa0;
    --ink: #555053;
    --grey: #8a8688;
    --photo: #6a605e;
    --rule: #b7b2b3;
  }
  * { margin: 0; padding: 0; box-sizing: border-box; }
  html, body {
    width: 1200px; height: 960px; overflow: hidden;
    background: radial-gradient(ellipse at center, #5a5a5a 0%, var(--backdrop) 75%);
    font-family: "Jost", sans-serif;
  }
  .card {
    position: absolute; left: 160px; top: 195px;
    width: 880px; height: 570px;
    background: var(--card);
    overflow: hidden;
    box-shadow: 0 20px 40px rgba(0,0,0,.45);
  }
  .portrait {
    position: absolute; left: 580px; top: 40px;
    width: 300px; height: 440px;
    background: var(--photo);
    border-radius: 130px 130px 0 0;
  }
  .identity { position: absolute; left: 70px; top: 120px; }
  .identity .name {
    font-weight: 300; font-size: 38px; color: var(--pink);
    letter-spacing: 0.5px; line-height: 1;
  }
  .identity .role {
    font-weight: 300; font-size: 28px; color: var(--grey);
    line-height: 1; margin-top: 2px;
  }
  .brand {
    position: absolute; left: 140px; top: 210px;
    font-weight: 500; font-size: 72px; color: var(--pink);
    letter-spacing: 0.5px; line-height: 1;
    white-space: nowrap;
  }
  .contacts {
    position: absolute; left: 150px; top: 325px;
    font-weight: 400; font-size: 25px; color: var(--ink);
    line-height: 32px; list-style: none;
  }
  .contacts .label { color: var(--pink-light); }
  .band { position: absolute; left: 0; bottom: 0; width: 880px; height: 130px; }
  .band-text {
    position: absolute; left: 140px; bottom: 28px;
    font-weight: 400; font-size: 30px; color: #fff; letter-spacing: 1px;
    white-space: nowrap;
  }
  .band-text .sep { margin: 0 14px; }
</style>
</head>
<body>
  <article class="card">
    <div class="portrait" role="img" aria-label="Portrait photo of the agent"></div>

    <div class="identity">
      <p class="name">RUI ALMEIDA</p>
      <p class="role">CEO/FOUNDER</p>
    </div>

    <p class="brand">Lumi Brasa</p>

    <ul class="contacts">
      <li><span class="label">Fax : </span>(+351) 210 555 148</li>
      <li><span class="label">Web : </span>Lumibrasa.com</li>
      <li>Rua das Amoreiras, 57</li>
      <li>4400-210, Vila Nova de Gaia</li>
    </ul>

    <svg class="band" viewBox="0 0 880 130" aria-hidden="true">
      <defs>
        <linearGradient id="bandFill" x1="0" x2="1" y1="0" y2="0">
          <stop offset="0" stop-color="#ee5fa3"/>
          <stop offset="0.35" stop-color="#e3237f"/>
          <stop offset="1" stop-color="#e3237f"/>
        </linearGradient>
      </defs>
      <path d="M0 56 L560 56 Q690 56 760 22 Q800 4 880 4" fill="none" stroke="var(--rule)" stroke-width="6"/>
      <path d="M0 60 L560 60 Q690 60 760 26 Q800 8 880 8 L880 130 L0 130 Z" fill="url(#bandFill)"/>
    </svg>
    <p class="band-text">(+351) 210 555 140<span class="sep">|</span>geral@lumibrasa.com</p>
  </article>
</body>
</html>
```